Stationery Design Project for Nimbora, Chicago

Nimbora, a street parking application which helps car drivers find a street parking spot by offering an ideal path along which to look for parking. This path is calculated by our algorithm based on data (e.g. historical data, baseball games schedule, etc.). Along this path the driver will find a spot and will also save 70% of the search time. Customer we target is reg. between 21 and 45 yo.

We envision something young, fresh, bright and original. Slightly abstract maybe. It should represent the idea and elements of finding street parking in the city, e.g. car(s), parking spot, people, city, etc. (just ideas!).

Logo is attached.

Requirement:
- Business Cards (2 Sided Full Color CMYK)
- Letterhead (1 Sided Full Color CMYK)
- Envelope (1 Sided Full Color CMYK)
- Sticker (1 Sided Full Color CMYK), round with a 2inch diameter.

Reason: We're starting to get more and more designs and need more time to look into all of them. Very exciting!! Thanks to everybody!

Hi all, we're in the process of selecting our favs. Though choices!!! Really good submissions. Will keep you posted and sorry for the delay.

Target Market(s)

Car drivers and owners between 21 and 45

Industry/Entity Type

Parking

Requirements
Must have
• Sticker should be round and include company URL nimbora.com and the new logo which we will attach soon.
Should not have
• Should not be too serious or boring.

```html
<!DOCTYPE html>
<html lang="en">
<head>
<meta charset="utf-8">
<title>Nimbora Business Card</title>
<link rel="stylesheet" href="https://fonts.googleapis.com/css2?family=Open+Sans:wght@400;600;700&display=swap">
<style>
  :root {
    --page-bg: #e9eaec;
    --card-light-top: #ffffff;
    --card-light-bottom: #d9dadc;
    --card-blue: #2b3a9c;
    --card-blue-light: #4a63c8;
    --brand-blue: #1f56c9;
    --brand-blue-dark: #14318f;
    --ink: #4a4a4c;
    --ink-dark: #1e1e20;
    --white: #ffffff;
    --photo-mid: #8d94b0;
    --photo-light: #c6c9d6;
  }
  * { margin: 0; padding: 0; box-sizing: border-box; }
  html, body { width: 954px; height: 1200px; overflow: hidden; }
  body {
    background: var(--page-bg);
    font-family: "Open Sans", Arial, sans-serif;
    position: relative;
  }
  .card {
    position: absolute;
    left: 91px;
    width: 797px;
    height: 454px;
    border-radius: 24px;
    overflow: hidden;
    box-shadow: 0 6px 14px rgba(0,0,0,0.25);
  }
  .card-front {
    top: 91px;
    background: linear-gradient(160deg, var(--card-light-top) 20%, var(--card-light-bottom) 100%);
  }
  .card-back {
    top: 660px;
    background: radial-gradient(ellipse at 45% 10%, var(--card-blue-light) 0%, var(--card-blue) 55%);
  }
  .brand-mark {
    position: absolute;
    border-radius: 50%;
    background: radial-gradient(circle at 40% 35%, var(--brand-blue) 0%, var(--brand-blue-dark) 100%);
    box-shadow: 0 0 0 10px rgba(255,255,255,0.35);
  }
  .card-front .brand-mark { left: 140px; top: 76px; width: 194px; height: 194px; }
  .brand-name {
    position: absolute;
    left: 63px;
    top: 318px;
    font-weight: 600;
    font-size: 88px;
    line-height: 1;
    color: var(--ink-dark);
    letter-spacing: -1px;
  }
  .contact-block { position: absolute; left: 473px; top: 60px; color: var(--ink); }
  .person { font-size: 25px; line-height: 1.3; }
  .person strong { font-weight: 700; }
  .person .role { font-size: 19px; }
  .address { margin-top: 36px; font-size: 19.5px; line-height: 33px; }
  .channels { list-style: none; margin-top: 40px; font-size: 19.5px; line-height: 32.5px; }
  .channels li { display: flex; align-items: center; gap: 10px; }
  .channels svg { width: 17px; height: 17px; fill: var(--ink); flex: none; }
  .photo-area {
    position: absolute;
    left: 63px; top: 40px;
    width: 580px; height: 350px;
    background: radial-gradient(ellipse at 50% 50%, var(--photo-light) 0%, var(--photo-mid) 50%, rgba(43,58,156,0) 78%);
  }
  .card-back .brand-mark {
    left: 514px; top: 105px; width: 220px; height: 220px;
    display: flex; align-items: center; justify-content: center;
  }
  .card-back .brand-mark span { font-weight: 600; font-size: 38px; color: var(--white); }
  .web-address {
    position: absolute; left: 165px; top: 404px;
    font-size: 23px; letter-spacing: 3.5px; color: var(--white);
  }
</style>
</head>
<body>
  <section class="card card-front">
    <div class="brand-mark"></div>
    <div class="brand-name">nimbora</div>
    <div class="contact-block">
      <p class="person"><strong>Your Name</strong> <span class="role">| Designation</span></p>
      <p class="address">City Name, Street Name<br>State Name, Country Code</p>
      <ul class="channels">
        <li><svg viewBox="0 0 16 16"><path d="M2 5c0-2 3-3 6-3s6 1 6 3v1h-3V5H5v1H2zM4 7h8l2 7H2z"/></svg>123-456-7890</li>
        <li><svg viewBox="0 0 16 16"><path d="M4 1h8v4H4zM1 6h14v6h-3v3H4v-3H1zm4 4v4h6v-4z"/></svg>123-456-7890</li>
        <li><svg viewBox="0 0 16 16"><path d="M1 3h14v10H1zm1.5 1.5L8 9l5.5-4.5v-.2h-11z"/></svg>name@website.com</li>
        <li><svg viewBox="0 0 16 16"><circle cx="8" cy="8" r="7"/><path d="M1 8h14M8 1c-3 3-3 11 0 14M8 1c3 3 3 11 0 14" stroke="#fff" stroke-width="1" fill="none"/></svg>www.website.com</li>
      </ul>
    </div>
  </section>

  <section class="card card-back">
    <div class="photo-area" role="img" aria-label="Aerial photo of cars parked in street parking bays with a cyclist passing"></div>
    <div class="brand-mark"><span>nimbora</span></div>
    <p class="web-address">www.website.com</p>
  </section>
</body>
</html>
```